A Techincal Author needs a site to promote his Programming Books

The StudyAlong series is a collection of books focusing on building the same app with different technologies. The purpose of this project is to design a web site home page that can be used to sell the books.

Expected Deliverables
• StudyAlong Logo as Illustrator file
• Master graphic design files for any relevant web assets
• HTML and CSS for home page, if applicable

Target Market(s)

The target market for our series is web programmers. They are people who have some experience, but want to learn a new tool. Programmers are analytical, logical people who like structure in the things they do.

Here are some things our customers like:

• Chirply / Postbox
• Crown of Ashes / Hollow Tide / Salt Hollow
• SmartPhones, Tablets, Stridelets, and other tech gadgets.

The design should try to speak to that market.

Requirements
Must have
• The primary tasks for this project are:
• 1) Create "Study Along" Logo.
• * All “NetPivot” properties use a similar logo approach, with the NetPivot ball icon on the left, a reflection below it. The company name is on the right, roughly the same size as the ball icon. A tag line underneath the company name, roughly the same size as the reflection.
• * Company Name: Study Along
• * Tagline: Knowledge to Boost Your Career
• * Logo color is up to the discretion of the designer, but should be compatible with the site design.
• * Sample Logos for other NetPivot properties in Illustrator format are available as attachments to this project.
• 2) Design the Study Along Home Page.
• The home page should follow this format:
• * Logo
• * Nav Bar
• • Buy (The Home Page)
• • About
• • Contact
• * Main Content
• • Home page content detailed in attachment
• * Footer
• • Copyright notice
• • Links to other stuff we do ( net-pivot.example | marlonpeake.example | BeyondTheGrid.example )
Nice to have
• It would be nice to have a book as part of the home page content.
Should not have
• Please do not use the same color scheme as BeyondTheGrid.example or Plumvane.example or QueryTheMaven.example

```html
<!DOCTYPE html>
<html lang="en">
<head>
<meta charset="utf-8">
<title>Study Along – Home</title>
<link href="https://fonts.googleapis.com/css2?family=Open+Sans:wght@400;600;700;800&family=Raleway:wght@600;700;800&display=swap" rel="stylesheet">
<style>
:root{
  --red:#c1272d;
  --red-dark:#a81f25;
  --ink:#333333;
  --muted:#777777;
  --line:#e3e3e3;
  --footer:#262626;
  --footer-text:#bdbdbd;
  --white:#ffffff;
}
*{margin:0;padding:0;box-sizing:border-box}
html,body{width:1200px;height:2164px;overflow:hidden;background:var(--white)}
body{font-family:"Open Sans",Arial,sans-serif;color:var(--ink);position:relative}
.page{position:relative;width:1200px;height:2164px}

/* header */
.site-header{position:absolute;top:0;left:0;width:1200px;height:96px;background:var(--white);border-bottom:1px solid var(--line)}
.brand{position:absolute;left:96px;top:22px;display:flex;align-items:center;gap:10px}
.brand-dot{width:26px;height:26px;border-radius:50%;background:var(--red)}
.brand-name{font-family:"Raleway",sans-serif;font-weight:800;font-size:25px;color:var(--red);line-height:1}
.brand-tag{position:absolute;left:132px;top:52px;font-size:9px;color:var(--muted);letter-spacing:.5px}
.top-phone{position:absolute;right:96px;top:16px;display:flex;align-items:center;gap:8px;font-size:13px;color:var(--ink)}
.main-nav{position:absolute;right:96px;top:54px;display:flex;gap:26px}
.main-nav a{font-size:12px;font-weight:700;color:var(--ink);text-decoration:none;letter-spacing:.3px;padding:6px 10px}
.main-nav a.active{background:var(--red);color:var(--white)}

/* hero */
.hero{position:absolute;top:96px;left:0;width:1200px;height:520px;background:linear-gradient(160deg,#8e7a63 0%,#b9a891 35%,#6f6a63 65%,#3f3b38 100%)}
.hero-shade{position:absolute;inset:0;background:linear-gradient(180deg,rgba(0,0,0,0) 40%,rgba(0,0,0,.45) 100%)}
.hero-title{position:absolute;top:330px;width:100%;text-align:center;color:var(--white);font-family:"Raleway",sans-serif;font-weight:800;font-size:36px;letter-spacing:1px}
.hero-sub{position:absolute;top:380px;left:300px;width:600px;text-align:center;color:var(--white);font-size:15px;font-weight:600;line-height:22px;letter-spacing:.3px}
.hero-dots{position:absolute;top:462px;width:100%;display:flex;justify-content:center;gap:8px}
.hero-dots span{width:11px;height:11px;border-radius:50%;border:2px solid var(--white)}
.hero-dots span.on{background:var(--white)}

/* welcome */
.welcome{position:absolute;top:616px;left:0;width:1200px;height:340px;background:var(--white)}
.section-heading{display:flex;align-items:center;gap:10px;font-family:"Raleway",sans-serif;font-weight:800;font-size:24px;color:var(--ink);letter-spacing:.5px}
.section-heading .mark{width:22px;height:22px;border-radius:50%;border:3px solid var(--red)}
.heading-rule{height:3px;width:70px;background:var(--red);margin-top:10px}
.welcome .section-heading{position:absolute;left:96px;top:46px}
.welcome .heading-rule{position:absolute;left:96px;top:78px;margin:0}
.welcome-text{position:absolute;left:96px;top:110px;width:560px;font-size:12px;line-height:21px;color:var(--muted)}
.btn{display:inline-block;background:var(--red);color:var(--white);font-size:11px;font-weight:700;letter-spacing:.5px;padding:10px 20px;text-decoration:none}
.welcome .btn{position:absolute;left:96px;top:280px}
.welcome-photo{position:absolute;right:0;top:20px;width:500px;height:320px;background:linear-gradient(135deg,#f1f1f1 0%,#d8c3b0 45%,#8b6b57 100%)}

/* courses */
.courses{position:absolute;top:956px;left:0;width:1200px;height:576px;background:linear-gradient(135deg,#5a5048 0%,#3b3632 50%,#2a2826 100%)}
.courses-shade{position:absolute;inset:0;background:rgba(20,20,20,.55)}
.courses .section-heading{position:absolute;top:60px;left:0;width:100%;justify-content:center;color:var(--white)}
.courses .section-heading .mark{border-color:var(--white)}
.courses .heading-rule{position:absolute;top:94px;left:565px;margin:0}
.course-grid{position:absolute;top:150px;left:150px;width:900px;display:grid;grid-template-columns:repeat(3,300px);row-gap:52px}
.course{text-align:center;color:var(--white)}
.course svg{display:block;margin:0 auto 10px}
.course h3{font-size:13px;font-weight:700;letter-spacing:.5px;margin-bottom:6px}
.course p{font-size:11px;line-height:17px;color:#d6d6d6;width:220px;margin:0 auto}
.courses .btn-ghost{position:absolute;top:498px;left:532px;width:136px;text-align:center;border:2px solid var(--white);color:var(--white);font-size:11px;font-weight:700;padding:9px 0;letter-spacing:.5px}

/* news */
.news{position:absolute;top:1532px;left:0;width:1200px;height:336px;background:var(--white)}
.news .section-heading{position:absolute;top:50px;left:0;width:100%;justify-content:center}
.news .heading-rule{position:absolute;top:84px;left:565px;margin:0}
.news-card{position:absolute;top:140px;width:470px;height:150px;display:flex;gap:18px}
.news-card.first{left:100px}
.news-card.second{left:630px}
.news-thumb{width:190px;height:150px;flex:none;background:linear-gradient(135deg,#d9dfe6 0%,#9fb0c0 50%,#6c7f91 100%)}
.news-body h4{font-size:12px;font-weight:700;color:var(--red);line-height:17px;letter-spacing:.3px}
.news-meta{font-size:10px;color:#999;margin:6px 0}
.news-body p{font-size:11px;line-height:17px;color:var(--muted)}
.news-body a{display:inline-block;margin-top:6px;font-size:11px;font-weight:700;color:var(--red);text-decoration:none}

/* footer */
.site-footer{position:absolute;top:1868px;left:0;width:1200px;height:252px;background:var(--footer);color:var(--footer-text)}
.footer-brand{position:absolute;left:96px;top:88px;display:flex;align-items:center;gap:10px}
.footer-brand .dot{width:24px;height:24px;border-radius:50%;background:var(--white)}
.footer-brand span{font-family:"Raleway",sans-serif;font-weight:800;font-size:24px;color:var(--white)}
.footer-col{position:absolute;top:40px}
.footer-col h5{font-size:13px;font-weight:700;color:var(--white);letter-spacing:.5px;margin-bottom:12px}
.footer-col ul{list-style:none}
.footer-col li{font-size:11px;line-height:20px}
.footer-col li::before{content:"›";color:var(--red);margin-right:6px}
.col-links{left:390px}
.col-news{left:608px;width:250px}
.field{display:flex;align-items:center;gap:8px;height:30px;background:var(--white);color:#999;font-size:11px;padding:0 10px;margin-bottom:10px}
.field i{width:10px;height:10px;border-radius:50%;background:var(--red);display:block}
.col-news .btn{padding:8px 18px}
.col-address{left:930px;width:200px}
.addr-row{display:flex;gap:10px;font-size:11px;line-height:16px;margin-bottom:14px}
.addr-row svg{flex:none}
.bottom-bar{position:absolute;top:2120px;left:0;width:1200px;height:44px;background:var(--red);color:var(--white);font-size:11px}
.bottom-bar .copy{position:absolute;left:96px;top:14px}
.socials{position:absolute;right:96px;top:12px;display:flex;gap:6px}
.socials span{width:20px;height:20px;border-radius:50%;border:1px solid var(--white)}
</style>
</head>
<body>
<div class="page">

  <header class="site-header">
    <div class="brand"><div class="brand-dot"></div><div class="brand-name">study-along.example</div></div>
    <div class="brand-tag">Knowledge to Boost Your Career</div>
    <div class="top-phone">
      <svg width="22" height="22" viewBox="0 0 22 22"><circle cx="11" cy="11" r="10" fill="none" stroke="#c1272d" stroke-width="1.5"/><path d="M7 6c1-1 2 0 2.5 1.5.3 1-.7 1.3-.5 2 .5 1.5 1.5 2.5 3 3 .7.2 1-.8 2-.5C15.5 12.5 16.5 13.5 15.5 14.5 13 17 5 9 7 6z" fill="#c1272d"/></svg>
      555 0142 310
    </div>
    <nav class="main-nav">
      <a class="active" href="#">HOME</a><a href="#">ABOUT US</a><a href="#">SERVICES</a><a href="#">NEWS</a><a href="#">TESTIMONIALE</a><a href="#">CONTACT US</a>
    </nav>
  </header>

  <section class="hero">
    <div role="img" aria-label="Students lying on a wooden floor reading books and working on a laptop" style="position:absolute;inset:0"></div>
    <div class="hero-shade"></div>
    <h1 class="hero-title">KNOWLEDGE TO BOOST YOUR CAREER</h1>
    <p class="hero-sub">STUDY-ALONG.EXAMPLE IS A COLLECTION OF BOOKS FOCUSING ON BUILDING THE SAME APP WITH DIFFERENT TECHNOLOGIES.</p>
    <div class="hero-dots"><span class="on"></span><span></span><span></span><span></span></div>
  </section>

  <section class="welcome">
    <h2 class="section-heading"><span class="mark"></span>WELCOME TO STUDY-ALONG.EXAMPLE</h2>
    <div class="heading-rule"></div>
    <p class="welcome-text">Every book in this series walks you through one complete project, built again and again with a new tool each time. You start from an empty folder and finish with a working app, learning how each framework handles data, screens, state and testing. Because the app stays the same, the differences between technologies become clear and easy to compare. Each chapter is short, practical and written for developers who already know the basics and want to add a fresh skill to their daily work without wasting a single evening on theory alone. Pick a stack, follow along, and see real progress by the very first weekend.</p>
    <a class="btn" href="#">LEARN MORE</a>
    <div class="welcome-photo" role="img" aria-label="Group of smiling students gathered together"></div>
  </section>

  <section class="courses">
    <div role="img" aria-label="Students studying together at a table, darkened background" style="position:absolute;inset:0"></div>
    <div class="courses-shade"></div>
    <h2 class="section-heading"><span class="mark"></span>OUR COURSE</h2>
    <div class="heading-rule"></div>
    <div class="course-grid">
      <div class="course">
        <svg width="36" height="36" viewBox="0 0 36 36" fill="none" stroke="#fff" stroke-width="2"><circle cx="18" cy="18" r="15"/><ellipse cx="18" cy="18" rx="7" ry="15"/><path d="M3 18h30M6 10h24M6 26h24"/></svg>
        <h3>LANGUAGE &amp; CULTURES</h3>
        <p>Short lessons on the words and ideas every new tool brings along with it.</p>
      </div>
      <div class="course">
        <svg width="36" height="36" viewBox="0 0 36 36" fill="none" stroke="#fff" stroke-width="2"><path d="M4 32h28"/><rect x="7" y="20" width="5" height="12"/><rect x="16" y="13" width="5" height="19"/><rect x="25" y="6" width="5" height="26"/></svg>
        <h3>BUSINESS &amp; MANAGEMENT</h3>
        <p>Plan, ship and maintain real projects with clear steps and simple habits.</p>
      </div>
      <div class="course">
        <svg width="36" height="36" viewBox="0 0 36 36" fill="none" stroke="#fff" stroke-width="2"><path d="M14 4h8M15 4v11L6 31h24L21 15V4"/></svg>
        <h3>SCIENCE, MATH &amp; SOCIAL</h3>
        <p>The logic behind the code, explained with small and friendly examples.</p>
      </div>
      <div class="course">
        <svg width="36" height="36" viewBox="0 0 36 36" fill="none" stroke="#fff" stroke-width="2"><rect x="4" y="6" width="28" height="19"/><path d="M13 31h10M18 25v6"/></svg>
        <h3>TEACHING &amp; STUDING</h3>
        <p>Guided exercises that help each new concept stick after every chapter.</p>
      </div>
      <div class="course">
        <svg width="36" height="36" viewBox="0 0 36 36" fill="none" stroke="#fff" stroke-width="2"><path d="M18 31S4 22 4 13a7 7 0 0 1 14-2 7 7 0 0 1 14 2c0 9-14 18-14 18z"/></svg>
        <h3>HEALTHY &amp; PSYCOLOGY</h3>
        <p>Keep learning steady and calm with pacing tips built into each book.</p>
      </div>
      <div class="course">
        <svg width="36" height="36" viewBox="0 0 36 36" fill="none" stroke="#fff" stroke-width="2"><circle cx="18" cy="18" r="14"/><circle cx="12" cy="14" r="2"/><circle cx="20" cy="10" r="2"/><circle cx="25" cy="17" r="2"/></svg>
        <h3>ARTS &amp; MEDIA</h3>
        <p>Design clean screens and layouts that users enjoy from the first click.</p>
      </div>
    </div>
    <a class="btn-ghost" href="#" style="text-decoration:none">VIEW MORE</a>
  </section>

  <section class="news">
    <h2 class="section-heading"><span class="mark"></span>LATEST NEWS</h2>
    <div class="heading-rule"></div>
    <article class="news-card first">
      <div class="news-thumb" role="img" aria-label="Students working at laptops in a classroom"></div>
      <div class="news-body">
        <h4>PERSPICIATIS UNDE OMNIS ISTE NATUS ERROR</h4>
        <div class="news-meta">May 18, 2016 &nbsp;|&nbsp; 10 comment</div>
        <p>A new volume is on the way, rebuilding the sample app with a fresh framework and a few extra chapters.</p>
        <a href="#">Read More »</a>
      </div>
    </article>
    <article class="news-card second">
      <div class="news-thumb" role="img" aria-label="Young learners reading together at a desk"></div>
      <div class="news-body">
        <h4>PERSPICIATIS UNDE OMNIS ISTE NATUS ERROR</h4>
        <div class="news-meta">May 18, 2016 &nbsp;|&nbsp; 10 comment</div>
        <p>Readers can now grab the full source code for every book and compare each version side by side.</p>
        <a href="#">Read More »</a>
      </div>
    </article>
  </section>

  <footer class="site-footer">
    <div class="footer-brand"><div class="dot"></div><span>Beyond The Grid</span></div>
    <div class="footer-col col-links">
      <h5>QUICK LINKS</h5>
      <ul><li>Home</li><li>About Us</li><li>Services</li><li>News</li><li>Testimonials</li><li>Contact</li></ul>
    </div>
    <div class="footer-col col-news">
      <h5>NEWS LETTER</h5>
      <div class="field"><i></i>Your Name</div>
      <div class="field"><i></i>Email Address</div>
      <a class="btn" href="#">SUBMIT</a>
    </div>
    <div class="footer-col col-address">
      <h5>ADDRESS</h5>
      <div class="addr-row">
        <svg width="12" height="16" viewBox="0 0 12 16"><path d="M6 0a6 6 0 0 0-6 6c0 4.5 6 10 6 10s6-5.5 6-10a6 6 0 0 0-6-6zm0 8.5A2.5 2.5 0 1 1 6 3.5a2.5 2.5 0 0 1 0 5z" fill="#c1272d"/></svg>
        <span>24 Harbor Lane, Suite 12<br>Maple Town, 00000</span>
      </div>
      <div class="addr-row">
        <svg width="12" height="14" viewBox="0 0 12 14"><path d="M1 1c1-1 2 0 2.5 1.5.3 1-.7 1.3-.5 2 .5 1.5 1.5 2.5 3 3 .7.2 1-.8 2-.5 1.5.5 2.5 1.5 1.5 2.5C7 12 -1 4 1 1z" fill="#c1272d"/></svg>
        <span>555 0142 310</span>
      </div>
      <div class="addr-row">
        <svg width="14" height="10" viewBox="0 0 14 10"><rect x=".5" y=".5" width="13" height="9" fill="none" stroke="#c1272d"/><path d="M.5.5 7 6l6.5-5.5" fill="none" stroke="#c1272d"/></svg>
        <span>contact@study-along.example</span>
      </div>
    </div>
  </footer>
  <div class="bottom-bar">
    <div class="copy">Copyright © study-along.example 2016. All rights reserved.</div>
    <div class="socials"><span></span><span></span><span></span><span></span><span></span></div>
  </div>

</div>
</body>
</html>
```